Moravel Aesthetic Doctor

I require an elegant, luxurious looking business card for my aesthetic business. I am a doctor and that will set me aside from competitors. I am planning to provide home and spa based treatments to clients with high expectations. I have attached my logo.

```html
<!DOCTYPE html>
<html lang="en">
<head>
<meta charset="utf-8">
<title>Moravel Aesthetic Doctor – Business Card</title>
<link rel="stylesheet" href="https://fonts.googleapis.com/css2?family=Cinzel:wght@400;500&family=Open+Sans:wght@400;600;700&display=swap">
<style>
  :root {
    --backdrop: #e6e9ee;
    --card: #ffffff;
    --ink-grey: #8a8d91;
    --ink-dark: #6f7276;
    --brand-blue: #2aa3d9;
    --brand-deep: #3560b5;
    --brand-light: #8fd3ec;
    --swoosh-grey: #b9bcc0;
  }
  * { margin: 0; padding: 0; box-sizing: border-box; }
  html, body { width: 1200px; height: 900px; overflow: hidden; }
  body {
    background: var(--backdrop);
    font-family: "Open Sans", Arial, sans-serif;
    position: relative;
  }
  .card {
    position: absolute;
    top: 155px;
    width: 360px;
    height: 590px;
    background: var(--card);
    overflow: hidden;
    box-shadow: 0 6px 18px rgba(40, 50, 70, 0.18);
  }
  .card--front { left: 180px; }
  .card--back { left: 660px; }
  .card__wave { position: absolute; left: 0; top: 0; width: 360px; height: 590px; }

  .brand { display: flex; align-items: center; gap: 12px; }
  .brand__dot {
    width: 46px; height: 46px; border-radius: 50%;
    background: var(--brand-blue);
    flex: none;
  }
  .brand__name {
    font-family: "Cinzel", Georgia, serif;
    color: var(--brand-blue);
    font-weight: 400;
    line-height: 1.15;
  }
  .brand__name span { display: block; }
  .brand__name .brand__main { font-size: 30px; letter-spacing: 2px; }
  .brand__name .brand__sub { font-size: 12.5px; letter-spacing: 1.6px; }

  /* front */
  .card--front .brand { position: absolute; top: 52px; left: 40px; }
  .doctor { position: absolute; top: 145px; left: 0; width: 360px; text-align: center; }
  .doctor__name {
    font-family: "Cinzel", Georgia, serif;
    font-weight: 400;
    color: var(--ink-grey);
    font-size: 27px;
    letter-spacing: 2px;
  }
  .doctor__credential { color: var(--brand-blue); font-size: 14px; margin-top: 6px; }
  .contact { position: absolute; top: 250px; left: 0; width: 360px; text-align: center; }
  .contact__icons { display: flex; justify-content: center; gap: 10px; margin-bottom: 8px; }
  .contact__icons svg { width: 15px; height: 15px; }
  .contact__line { color: var(--ink-grey); font-weight: 700; font-size: 15px; line-height: 1.6; }
  .social { display: flex; justify-content: center; gap: 34px; margin-top: 14px; }
  .social__square { width: 22px; height: 22px; background: var(--brand-blue); border-radius: 3px; }

  /* back */
  .services { position: absolute; top: 44px; left: 58px; }
  .services__title {
    font-family: "Cinzel", Georgia, serif;
    color: var(--ink-grey);
    font-size: 25px;
    letter-spacing: 1.5px;
    text-decoration: underline;
    text-underline-offset: 4px;
    text-decoration-thickness: 1px;
  }
  .services__list { list-style: none; margin-top: 14px; margin-left: 26px; }
  .services__list li {
    color: var(--ink-grey); font-weight: 700; font-size: 15px;
    display: flex; align-items: center; gap: 16px; line-height: 1.8;
  }
  .services__list li::before {
    content: ""; width: 10px; height: 10px; border-radius: 50%;
    background: var(--brand-blue); flex: none;
  }
  .tagline {
    position: absolute; top: 246px; left: 0; width: 360px; text-align: center;
    font-family: "Cinzel", Georgia, serif;
    color: var(--brand-blue); font-size: 21px; letter-spacing: 1.5px; line-height: 1.6;
  }
  .card--back .brand { position: absolute; top: 326px; right: 22px; gap: 8px; }
  .card--back .brand__dot { width: 34px; height: 34px; }
  .card--back .brand__main { font-size: 22px; }
  .card--back .brand__sub { font-size: 9.5px; }
</style>
</head>
<body>

<section class="card card--front" aria-label="Business card front">
  <svg class="card__wave" viewBox="0 0 360 590" aria-hidden="true">
    <defs>
      <linearGradient id="bandFront" x1="0" y1="1" x2="1" y2="0">
        <stop offset="0" stop-color="#3fb0d9"/>
        <stop offset="0.45" stop-color="#8fd3ec"/>
        <stop offset="1" stop-color="#3560b5"/>
      </linearGradient>
    </defs>
    <path d="M0,440 C150,432 295,392 360,300 L360,322 C300,405 160,448 0,458 Z" fill="#b9bcc0"/>
    <path d="M0,462 C165,452 305,410 360,330 L360,590 L0,590 Z" fill="url(#bandFront)"/>
  </svg>

  <div class="brand">
    <div class="brand__dot"></div>
    <p class="brand__name"><span class="brand__main">MORAVEL</span><span class="brand__sub">AESTHETIC DOCTOR</span></p>
  </div>

  <div class="doctor">
    <h1 class="doctor__name">DR ELISE VARNOW</h1>
    <p class="doctor__credential">MRCPCH MD</p>
    <p class="doctor__credential">Australasian Diploma of Aesthetic Medicine</p>
  </div>

  <div class="contact">
    <div class="contact__icons">
      <svg viewBox="0 0 16 16" aria-label="Phone"><path d="M4 2l2.5 3-1.5 1.5c.8 1.8 2.2 3.2 4 4L10.5 9l3 2.5-1.5 2.5C7 14 2 9 2 3.5z" fill="#2aa3d9"/></svg>
      <svg viewBox="0 0 16 16" aria-label="Email"><rect x="1.5" y="3.5" width="13" height="9" fill="none" stroke="#2aa3d9" stroke-width="1.4"/><path d="M1.5 3.5L8 9l6.5-5.5" fill="none" stroke="#2aa3d9" stroke-width="1.4"/></svg>
      <svg viewBox="0 0 16 16" aria-label="Website"><circle cx="8" cy="8" r="6.3" fill="none" stroke="#2aa3d9" stroke-width="1.3"/><ellipse cx="8" cy="8" rx="2.8" ry="6.3" fill="none" stroke="#2aa3d9" stroke-width="1.1"/><path d="M1.8 8h12.4" stroke="#2aa3d9" stroke-width="1.1"/></svg>
    </div>
    <p class="contact__line">0800 555 014</p>
    <p class="contact__line">elise.moravel.co.nz</p>
    <p class="contact__line">www.moravel.co.nz</p>
    <div class="social">
      <div class="social__square"></div>
      <div class="social__square"></div>
    </div>
  </div>
</section>

<section class="card card--back" aria-label="Business card back">
  <svg class="card__wave" viewBox="0 0 360 590" aria-hidden="true">
    <defs>
      <linearGradient id="bandBack" x1="0" y1="1" x2="1" y2="0">
        <stop offset="0" stop-color="#3fb0d9"/>
        <stop offset="0.45" stop-color="#8fd3ec"/>
        <stop offset="1" stop-color="#3560b5"/>
      </linearGradient>
    </defs>
    <path d="M0,480 C150,472 295,432 360,370 L360,392 C300,445 160,488 0,498 Z" fill="#b9bcc0"/>
    <path d="M0,502 C165,492 305,450 360,400 L360,590 L0,590 Z" fill="url(#bandBack)"/>
  </svg>

  <div class="services">
    <h2 class="services__title">OUR SERVICES:</h2>
    <ul class="services__list">
      <li>Dermal injectables</li>
      <li>Microneedling</li>
      <li>Excessive sweating</li>
      <li>Plasma facials</li>
      <li>Skin boosters</li>
    </ul>
  </div>

  <p class="tagline">HOME AND SPA<br>BASED TREATMENTS</p>

  <div class="brand">
    <div class="brand__dot"></div>
    <p class="brand__name"><span class="brand__main">MORAVEL</span><span class="brand__sub">AESTHETIC DOCTOR</span></p>
  </div>
</section>

</body>
</html>
```